Zvo Klinieken website for a maxillofacial surgery clinic

It's a website for a clinic for maxillofacial surgery in WordPress . The website doesn't need to be complicated but has to look professional. It needs to be in Dutch so i can give the texts. Similar websites are www.tandartsenpraktijkveldorm.nl or www.pbtspecialisten.nl. Pages would be sort of similar to https://hetcentrumvoorgezichtszorg.nl/ or https://wervelmondclinics.nl/. Those lasts are maxillofacial surgery clinic websites, but there are little more extensive.
I uploaded the logo. If this is not the proper quality i can upload the eps. Logo was made through pixelforum.

Target Market(s)

Patients who can find me and see information about the clinic

Industry/Entity Type

Healthcare

Coding

Coded - Design and coding required

Number of Pages Required

5+ page

Font styles to use
Other font styles liked:
• Something standard professional

Colors
0054AA
0677BA
7BADD7
CADEEF
E8F1F8

Requirements
Nice to have
• Something in line with the logo. I prefer a little dark like the darker logos but I'm not sure if that's professional. Logos bkvzo and rlpw are instances i'm registered to so they will have to be on the website too but small somewhere.

```html
<!DOCTYPE html>
<html lang="nl">
<head>
<meta charset="utf-8">
<title>Zvo Klinieken Zoetermeer</title>
<link href="https://fonts.googleapis.com/css2?family=Montserrat:wght@400;500;600;700&display=swap" rel="stylesheet">
<style>
:root{
  --blue:#2a9fd8;
  --blue-deep:#2187c2;
  --blue-soft:#eaf6fc;
  --blue-photo:#cfeaf8;
  --ink:#1d1d1d;
  --muted:#6a6a6a;
  --grey-btn:#6b6b6b;
  --footer:#121212;
  --white:#ffffff;
  --star:#f4b400;
}
*{box-sizing:border-box;margin:0;padding:0}
html,body{width:1200px;height:4971px;overflow:hidden}
body{font-family:'Montserrat',sans-serif;color:var(--ink);background:var(--white);position:relative}
section,header,footer,.topbar{position:absolute;left:0;width:1200px}
.btn{position:absolute;display:flex;align-items:center;justify-content:center;font-weight:600;font-size:15px;border-radius:6px;color:var(--white)}
.btn-blue{background:var(--blue)}
.btn-grey{background:var(--grey-btn)}
.title{position:absolute;left:0;width:1200px;text-align:center;font-size:38px;font-weight:500;letter-spacing:.5px}
.arrow{position:absolute;width:22px;height:22px;border-radius:50%;background:var(--blue);display:flex;align-items:center;justify-content:center}

.topbar{top:0;height:42px;background:var(--blue);color:var(--white);font-size:13px}
.topbar .item{position:absolute;top:0;height:42px;display:flex;align-items:center;gap:8px}

header{top:42px;height:87px;background:var(--blue-soft)}
.logo-box{position:absolute;left:108px;top:6px;width:152px;height:114px;background:var(--white);border-radius:10px;box-shadow:0 2px 8px rgba(0,0,0,.18);display:flex;align-items:center;justify-content:center;gap:6px;z-index:3}
.logo-box .dot{width:14px;height:14px;border-radius:50%;background:var(--blue)}
.logo-box span{font-size:19px;font-weight:700;color:var(--blue);line-height:1.1}
nav{position:absolute;left:350px;top:0;height:87px;display:flex;align-items:center;gap:22px;font-size:14px;font-weight:500}

.hero{top:129px;height:539px;overflow:hidden}
.hero-photo{position:absolute;inset:0;
  background:
   radial-gradient(ellipse 170px 260px at 890px 330px,rgba(255,255,255,.95) 0%,rgba(255,255,255,.6) 55%,rgba(255,255,255,0) 100%),
   radial-gradient(circle 70px at 890px 110px,#c79b82 0%,#c79b82 60%,rgba(199,155,130,0) 100%),
   radial-gradient(ellipse 260px 200px at 200px 520px,#2f6f6a 0%,rgba(47,111,106,0) 100%),
   linear-gradient(90deg,#4f6f6c 0%,#7f9c98 30%,#b9cdcb 55%,#dfeaec 75%,#eef4f6 100%)}
.hero-text{position:absolute;left:110px;top:128px;color:var(--white)}
.hero-text .kicker{font-size:28px;font-weight:500}
.hero-text h1{font-size:49px;font-weight:500;line-height:1.05;margin-top:4px}
.hero-text p{font-size:17px;line-height:28px;margin-top:12px;width:390px;font-weight:500}
.btn-outline{left:114px;top:349px;width:238px;height:49px;border:2px solid var(--white);background:transparent}

.about{top:668px;height:510px}
.about-frame{position:absolute;left:130px;top:62px;width:420px;height:420px;border-radius:46% 46% 40% 40%;border:14px solid #5d7ea3;border-left-color:var(--blue);border-top-color:var(--blue)}
.about-photo{position:absolute;left:170px;top:100px;width:340px;height:340px;border-radius:50% 50% 44% 44%;background:radial-gradient(circle at 45% 42%,#f0d2c2 0%,#e3c2b0 25%,#a9d6e6 55%,#e9f1f4 100%)}
.about h2{position:absolute;left:598px;top:88px;font-size:38px;font-weight:500}
.about p{position:absolute;left:598px;top:152px;width:445px;font-size:13px;line-height:27.5px;color:var(--muted)}

.services{top:1178px;height:496px}
.service{position:absolute;top:136px;width:238px;height:262px;background:var(--white);border-radius:10px;box-shadow:0 1px 8px rgba(0,0,0,.18);text-align:center}
.service .icon{width:132px;height:132px;border-radius:50%;background:var(--blue);margin:36px auto 0;display:flex;align-items:center;justify-content:center}
.service .icon i{width:74px;height:74px;border-radius:50%;background:radial-gradient(circle,#ffffff 0%,#ffffff 58%,rgba(255,255,255,.25) 60%,rgba(255,255,255,0) 100%)}
.service .label{position:absolute;left:0;right:0;bottom:18px;font-size:21px;font-weight:500;line-height:30px;display:flex;align-items:flex-end;justify-content:center;height:64px}

.surgery{top:1674px;height:984px;background:var(--blue);color:var(--white)}
.surgery p{position:absolute;left:225px;width:750px;top:156px;text-align:center;font-size:13px;line-height:27.5px}
.compare{position:absolute;left:110px;top:389px;width:976px;height:434px;display:flex;gap:3px}
.compare .half{flex:1}
.before{background:radial-gradient(ellipse 150px 190px at 50% 42%,#d9d6d2 0%,#b9b5b1 45%,rgba(150,150,150,0) 100%),linear-gradient(180deg,#8f8f8f,#6a6a6a)}
.after{background:radial-gradient(ellipse 150px 190px at 45% 42%,#e8d6c8 0%,#cbb8a8 45%,rgba(220,220,218,0) 100%),linear-gradient(180deg,#ececea,#d6d6d3)}
.handle{position:absolute;left:451px;top:180px;width:74px;height:74px;border-radius:50%;background:var(--blue);border:3px solid var(--white);display:flex;align-items:center;justify-content:center;gap:8px}
.vlabel{position:absolute;font-size:22px;font-weight:600;color:var(--white)}
.dot-nav{position:absolute;top:864px;width:18px;height:18px;border-radius:50%;background:var(--white)}
.dot-active{position:absolute;left:521px;top:858px;width:30px;height:30px;border-radius:50%;border:3px solid var(--white);display:flex;align-items:center;justify-content:center}
.dot-active i{width:16px;height:16px;border-radius:50%;background:var(--white)}

.team{top:2658px;height:640px}
.member{position:absolute;top:170px;width:318px;height:417px;background:var(--white);box-shadow:0 1px 8px rgba(0,0,0,.18);text-align:center}
.member .photo{height:318px;background:
  radial-gradient(ellipse 110px 120px at 50% 100%,#ffffff 0%,#f4f7f9 70%,rgba(244,247,249,0) 100%),
  radial-gradient(circle 42px at 50% 32%,#d7b29c 0%,#d7b29c 70%,rgba(215,178,156,0) 100%),
  linear-gradient(180deg,var(--blue-photo),#bfe1f3)}
.member .name{font-size:22px;font-weight:600;color:var(--blue);margin-top:18px}
.member .role{font-size:16px;font-weight:500;margin-top:10px}

.reviews{top:3298px;height:572px}
.review{position:absolute;top:113px;width:315px;height:360px;background:var(--white);box-shadow:0 1px 8px rgba(0,0,0,.18);text-align:center}
.review .avatar{width:112px;height:112px;border-radius:50%;background:radial-gradient(circle at 50% 40%,#d6a98c 0%,#d6a98c 30%,#c9dbe6 60%,#e3ecf1 100%);margin:22px auto 0}
.review .name{font-size:15px;font-weight:500;margin-top:14px}
.review .tag{font-size:14px;color:var(--blue);margin-top:4px}
.review .quote{position:absolute;left:14px;top:174px;font-size:34px;font-weight:700;line-height:1}
.review p{font-size:13px;line-height:26px;color:var(--muted);margin:22px 24px 0;text-align:center}
.stars{color:var(--star);font-size:18px;letter-spacing:1px;margin-top:4px}

.contact{top:3870px;height:727px;background:var(--blue);color:var(--white)}
.form-panel{position:absolute;left:107px;top:96px;width:483px;height:544px;background:var(--blue-deep);border-radius:6px}
.form-panel h2{position:absolute;left:26px;top:52px;font-size:38px;font-weight:600}
.field{position:absolute;left:26px;width:433px;height:50px;border:1.5px solid rgba(255,255,255,.7);border-radius:6px;font-size:12px;padding:14px 16px}
.contact h3{position:absolute;left:616px;top:74px;font-size:30px;font-weight:600}
.ci{position:absolute;display:flex;align-items:center;gap:10px;font-size:13px;font-weight:500;line-height:24px}
.ci .circ{width:40px;height:40px;border-radius:50%;border:2px solid var(--white);display:flex;align-items:center;justify-content:center;flex:none}
.map{position:absolute;left:616px;top:295px;width:454px;height:345px;border-radius:10px;background:radial-gradient(ellipse 120px 160px at 55% 45%,#c9ced3 0%,rgba(201,206,211,0) 100%),linear-gradient(135deg,#f3f5f6,#e0e4e7);overflow:hidden}
.map-pin{position:absolute;left:203px;top:118px;display:flex;flex-direction:column;align-items:center;gap:4px;color:#1d1d1d;font-size:17px;font-weight:600}

footer{top:4597px;height:374px;background:var(--footer);color:var(--white)}
.f-logo{position:absolute;left:110px;top:86px;display:flex;align-items:center;gap:8px;font-size:26px;font-weight:700;color:var(--blue)}
.f-logo .dot{width:18px;height:18px;border-radius:50%;background:var(--blue)}
.social{position:absolute;top:240px;width:30px;height:30px;border-radius:50%;border:2px solid var(--white)}
.col{position:absolute;top:78px}
.col h4{font-size:22px;font-weight:600;margin-bottom:16px}
.col a{display:block;font-size:13px;color:var(--white);text-decoration:none;line-height:30px}
.col .row{display:flex;gap:6px;font-size:13px;line-height:26px;align-items:flex-start}
.f-line{position:absolute;left:110px;top:306px;width:976px;height:1px;background:#777}
.copy{position:absolute;left:385px;top:333px;font-size:13px}
</style>
</head>
<body>

<div class="topbar">
  <div class="item" style="left:113px"><svg width="22" height="22" viewBox="0 0 22 22"><circle cx="11" cy="11" r="10" fill="#fff"/><path d="M11 5v6l4 2" stroke="#2a9fd8" stroke-width="2" fill="none"/></svg>Mon - Fri 10 Am To 6 Pm</div>
  <div class="item" style="left:508px"><svg width="24" height="24" viewBox="0 0 24 24"><circle cx="12" cy="12" r="11" fill="none" stroke="#fff" stroke-width="1.5"/><path d="M8 7l2-1 2 3-1.5 1.2a7 7 0 0 0 3.3 3.3L15 12l3 2-1 2c-4 0-9-5-9-9z" fill="#fff"/></svg>+1888 888 8888</div>
  <div class="item" style="left:788px"><svg width="24" height="24" viewBox="0 0 24 24"><circle cx="12" cy="12" r="11" fill="none" stroke="#fff" stroke-width="1.5"/><path d="M12 5a4 4 0 0 0-4 4c0 3 4 8 4 8s4-5 4-8a4 4 0 0 0-4-4z" fill="#fff"/><circle cx="12" cy="9" r="1.5" fill="#2a9fd8"/></svg>130,lorem Ipsum issimply dummy text</div>
</div>

<header>
  <div class="logo-box"><div class="dot"></div><span>Zvo<br>Klinieken</span></div>
  <nav><span>Thuis</span><span>Over ons</span><span>Onze locaties</span><span>Ons team</span><span>Contact</span></nav>
  <div class="btn btn-blue" style="left:847px;top:18px;width:238px;height:50px">Plan een afspraak</div>
</header>

<section class="hero">
  <div class="hero-photo" role="img" aria-label="Glimlachende chirurg in witte jas in een behandelkamer met tandartsstoel"></div>
  <div class="hero-text">
    <div class="kicker">WELKOM BIJ</div>
    <h1>ZVO KLINIEKEN<br>ZOETERMEER</h1>
    <p>Lorem Ipsum is simply dummy text of the printing and typesetting industry. Lorem</p>
  </div>
  <div class="btn btn-outline">Plan een afspraak</div>
</section>

<section class="about">
  <div class="about-frame"></div>
  <div class="about-photo" role="img" aria-label="Lachende vrouw tijdens een tandheelkundig onderzoek"></div>
  <h2>OVER ONS</h2>
  <p>Lorem Ipsum is simply dummy text of the printing and typesetting industry. Lorem Ipsum has been the industry's standard dummy text ever since the 1500s, when an unknown printer took a galley of type and scrambled it to make a type specimen book. It has survived not only five centuries, but also the leap into electronic typesetting, remaining essentially unchanged.Lorem Ipsum is simply dummy text of the printing and typesetting industry. Lorem Ipsum has been the industry's</p>
  <div class="btn btn-blue" style="left:598px;top:396px;width:197px;height:51px">Lees verder</div>
</section>

<section class="services">
  <div class="title" style="top:48px">ONZE DIENSTEN</div>
  <div class="arrow" style="left:34px;top:258px"><svg width="10" height="10" viewBox="0 0 10 10"><path d="M6.5 1.5L3 5l3.5 3.5" stroke="#fff" stroke-width="1.8" fill="none"/></svg></div>
  <div class="arrow" style="left:1140px;top:258px"><svg width="10" height="10" viewBox="0 0 10 10"><path d="M3.5 1.5L7 5 3.5 8.5" stroke="#fff" stroke-width="1.8" fill="none"/></svg></div>
  <div class="service" style="left:80px"><div class="icon" role="img" aria-label="Pictogram van een schedel"><i></i></div><div class="label">Bottransplantatie</div></div>
  <div class="service" style="left:344px"><div class="icon" role="img" aria-label="Pictogram van een gezicht met pijn"><i></i></div><div class="label">Chronische<br>gezichtspijn</div></div>
  <div class="service" style="left:610px"><div class="icon" role="img" aria-label="Pictogram van lippen"><i></i></div><div class="label">Gespleten lip en<br>gehemelte</div></div>
  <div class="service" style="left:874px"><div class="icon" role="img" aria-label="Pictogram van een gebit"><i></i></div><div class="label">Verbeter de<br>kaakvorm</div></div>
</section>

<section class="surgery">
  <div class="title" style="top:84px">MAXILLOFACIALE CHIRURGIE</div>
  <p>Lorem Ipsum is simply dummy text of the printing and typesetting industry. Lorem Ipsum has been the industry's standard dummy text ever since the 1500s, when an unknown printer took a galley of type and scrambled it to make a type specimen book. It has survived not only five centuries, but also the leap into electronic typesetting, remaining essentially unchanged.Lorem Ipsum is simply dummy text of the printing</p>
  <div class="btn btn-grey" style="left:496px;top:294px;width:207px;height:49px">Lees verder</div>
  <div class="vlabel" style="left:80px;top:486px;transform:rotate(-90deg);transform-origin:left top">Before</div>
  <div class="compare">
    <div class="half before" role="img" aria-label="Portret van een vrouw vóór de behandeling"></div>
    <div class="half after" role="img" aria-label="Portret van dezelfde vrouw na de behandeling"></div>
    <div class="handle"><svg width="12" height="16" viewBox="0 0 12 16"><path d="M10 1L2 8l8 7z" fill="#fff"/></svg><svg width="12" height="16" viewBox="0 0 12 16"><path d="M2 1l8 7-8 7z" fill="#fff"/></svg></div>
  </div>
  <div class="vlabel" style="left:1112px;top:740px;transform:rotate(90deg);transform-origin:left top">After</div>
  <div class="dot-active"><i></i></div>
  <div class="dot-nav" style="left:566px"></div>
  <div class="dot-nav" style="left:601px"></div>
  <div class="dot-nav" style="left:635px"></div>
</section>

<section class="team">
  <div class="title" style="top:92px">ONS TEAM</div>
  <div class="arrow" style="left:34px;top:378px"><svg width="10" height="10" viewBox="0 0 10 10"><path d="M6.5 1.5L3 5l3.5 3.5" stroke="#fff" stroke-width="1.8" fill="none"/></svg></div>
  <div class="arrow" style="left:1140px;top:378px"><svg width="10" height="10" viewBox="0 0 10 10"><path d="M3.5 1.5L7 5 3.5 8.5" stroke="#fff" stroke-width="1.8" fill="none"/></svg></div>
  <div class="member" style="left:107px"><div class="photo" role="img" aria-label="Portret van chirurg Alexandre in witte jas"></div><div class="name">Alexandre</div><div class="role">Chirurg</div></div>
  <div class="member" style="left:438px"><div class="photo" role="img" aria-label="Portret van chirurg Gabriel in witte jas"></div><div class="name">Gabriel</div><div class="role">Chirurg</div></div>
  <div class="member" style="left:768px"><div class="photo" role="img" aria-label="Portret van chirurg Rachel in witte jas"></div><div class="name">Rachel</div><div class="role">Chirurg</div></div>
</section>

<section class="reviews">
  <div class="title" style="top:34px">ONZE GETUIGENISSEN</div>
  <div class="arrow" style="left:34px;top:283px"><svg width="10" height="10" viewBox="0 0 10 10"><path d="M6.5 1.5L3 5l3.5 3.5" stroke="#fff" stroke-width="1.8" fill="none"/></svg></div>
  <div class="arrow" style="left:1140px;top:283px"><svg width="10" height="10" viewBox="0 0 10 10"><path d="M3.5 1.5L7 5 3.5 8.5" stroke="#fff" stroke-width="1.8" fill="none"/></svg></div>
  <div class="review" style="left:110px"><div class="avatar" role="img" aria-label="Portretfoto van Anderson"></div><div class="name">Anderson</div><div class="tag">Cliënt</div><div class="quote">“</div><p>Lorem Ipsum is simply dummy text of the printing and typesetting industry. Lorem Ipsum has been the industry's standard dummy text ever since the</p><div class="stars">★★★★★</div></div>
  <div class="review" style="left:443px"><div class="avatar" role="img" aria-label="Portretfoto van Robin"></div><div class="name">Robin</div><div class="tag">Cliënt</div><div class="quote">“</div><p>Lorem Ipsum is simply dummy text of the printing and typesetting industry. Lorem Ipsum has been the industry's standard dummy text ever since the</p><div class="stars">★★★★★</div></div>
  <div class="review" style="left:773px"><div class="avatar" role="img" aria-label="Portretfoto van Jessica"></div><div class="name">jessica</div><div class="tag">Cliënt</div><div class="quote">“</div><p>Lorem Ipsum is simply dummy text of the printing and typesetting industry. Lorem Ipsum has been the industry's standard dummy text ever since the</p><div class="stars">★★★★★</div></div>
</section>

<section class="contact">
  <div class="form-panel">
    <h2>PLAN EEN AFSPRAAK</h2>
    <div class="field" style="top:150px">Uw naam</div>
    <div class="field" style="top:208px">Email Address</div>
    <div class="field" style="top:268px">Telefoonnummer</div>
    <div class="field" style="top:328px;height:108px">Bericht</div>
    <div class="btn btn-grey" style="left:142px;top:454px;width:207px;height:48px">Bericht versturen</div>
  </div>
  <h3>Neem contact met ons op</h3>
  <div class="ci" style="left:616px;top:142px"><div class="circ"><svg width="16" height="20" viewBox="0 0 16 20"><path d="M8 1a6 6 0 0 0-6 6c0 5 6 12 6 12s6-7 6-12a6 6 0 0 0-6-6z" fill="#fff"/><circle cx="8" cy="7" r="2.2" fill="#2a9fd8"/></svg></div><span>130,lorem Ipsum issimply<br>dummy text printing</span></div>
  <div class="ci" style="left:866px;top:142px"><div class="circ"><svg width="18" height="18" viewBox="0 0 18 18"><path d="M3 2l3-1 3 4-2 1.5a9 9 0 0 0 4.5 4.5L13 9l4 3-1 3C9 15 3 9 3 2z" fill="#fff"/></svg></div><span>+1888 888 8888</span></div>
  <div class="ci" style="left:616px;top:228px"><div class="circ"><svg width="18" height="14" viewBox="0 0 18 14"><rect x="1" y="1" width="16" height="12" fill="#fff"/><path d="M1 1l8 7 8-7" stroke="#2a9fd8" stroke-width="1.5" fill="none"/></svg></div><span>Support@zvoklinieken.nl</span></div>
  <div class="map" role="img" aria-label="Kaart met de locatie van Zvo Klinieken">
    <div class="map-pin"><svg width="38" height="50" viewBox="0 0 16 20"><path d="M8 1a6 6 0 0 0-6 6c0 5 6 12 6 12s6-7 6-12a6 6 0 0 0-6-6z" fill="#c8102e"/><circle cx="8" cy="7" r="2.2" fill="#fff"/></svg>Zvo Klinieken</div>
  </div>
</section>

<footer>
  <div class="f-logo"><div class="dot"></div>Zvo Klinieken</div>
  <div class="social" style="left:109px"></div>
  <div class="social" style="left:159px"></div>
  <div class="col" style="left:382px"><h4>Main Links</h4><a>Thuis</a><a>Over ons</a><a>Onze locaties</a><a>Ons team</a><a>Contact</a></div>
  <div class="col" style="left:602px"><h4>Other Links</h4><a>Carrière</a><a>Voorwaarden</a><a>Privacybeleid</a></div>
  <div class="col" style="left:868px"><h4>Contact Us</h4>
    <div class="row"><span>✉</span>Support@zvoklinieken.nl</div>
    <div class="row"><span>✆</span>+1800 000 0000</div>
    <div class="row"><span>⦿</span>130,lorem Ipsum issimply<br>dummy text printing</div>
  </div>
  <div class="f-line"></div>
  <div class="copy">2023 Copyright © Zvo Klinieken zoetermeer | All Rights Reserved</div>
</footer>

</body>
</html>
```